Verodex business card

Business card for sustainable investment company called "Verodex". Verodex is an exchange platform selling carbon credits between buyers and sellers. Carbon Credits are an environmental commodity for reducing global carbon emissions.

the card should obviously have our logo and the theme should be sustainability/environment mixed with a trading platform.

Contact Information for Business Card

Logo, Name, Title, Phone, Email

Colors
0054AA
0677BA
7BADD7
CADEEF
E8F1F8
0094D4
00A9DD
6FCCEA
C7EBF8
E9F6FB
00AB8E
00BBA5
67D7C9
C6EFE9
E9F9F6
59FF00
82FF00
B8FF75
E3FFCB
F4FFEA

```html
<!DOCTYPE html>
<html lang="en">
<head>
<meta charset="utf-8">
<title>Verodex business card</title>
<link href="https://fonts.googleapis.com/css2?family=Montserrat:wght@400;500;700&display=swap" rel="stylesheet">
<style>
  :root {
    --bg: #3a3a3a;
    --navy: #1b2a4a;
    --blue-deep: #3f6bb8;
    --blue-mid: #2fb3e6;
    --cyan-light: #63c9dc;
    --accent: #35b6ea;
    --white: #ffffff;
    --ink: #1e1e1e;
  }
  * { box-sizing: border-box; margin: 0; padding: 0; }
  html, body { width: 1200px; height: 900px; overflow: hidden; }
  body {
    background: var(--bg);
    font-family: "Montserrat", sans-serif;
    position: relative;
  }
  .card {
    position: absolute;
    width: 600px;
    height: 343px;
    overflow: hidden;
    box-shadow: 0 10px 30px rgba(0,0,0,0.45);
  }
  /* Front */
  .card-front {
    left: 80px;
    top: 90px;
    background: linear-gradient(225deg, var(--blue-deep) 0%, var(--blue-mid) 55%, var(--cyan-light) 100%);
    display: flex;
    align-items: center;
    justify-content: center;
  }
  .brand {
    display: flex;
    align-items: center;
    gap: 18px;
  }
  .brand-square {
    width: 46px;
    height: 46px;
    background: var(--white);
  }
  .brand-name {
    font-weight: 700;
    font-size: 58px;
    letter-spacing: 2px;
    color: var(--white);
  }
  /* Back */
  .card-back {
    left: 520px;
    top: 470px;
    background: var(--white);
  }
  .back-brand {
    position: absolute;
    left: 44px;
    top: 110px;
    display: flex;
    align-items: center;
    gap: 12px;
  }
  .back-brand .brand-square {
    width: 30px;
    height: 30px;
    background: var(--accent);
  }
  .back-brand .brand-name {
    font-size: 36px;
    letter-spacing: 1px;
    color: var(--navy);
  }
  .person {
    position: absolute;
    right: 40px;
    top: 40px;
    text-align: right;
  }
  .person-name {
    font-weight: 700;
    font-size: 22px;
    letter-spacing: 0.5px;
    color: var(--navy);
  }
  .person-name .surname { color: var(--accent); }
  .person-title {
    font-size: 15px;
    font-weight: 500;
    color: var(--ink);
    margin-top: 2px;
  }
  .edge-tab {
    position: absolute;
    right: 0;
    top: 34px;
    width: 12px;
    height: 40px;
    background: var(--accent);
  }
  .contact {
    position: absolute;
    left: 44px;
    top: 200px;
    list-style: none;
    font-size: 15px;
    font-weight: 500;
    color: var(--ink);
  }
  .contact li {
    display: flex;
    align-items: center;
    gap: 10px;
    margin-bottom: 6px;
  }
  .contact svg { width: 16px; height: 16px; flex: none; }
  .wave {
    position: absolute;
    left: 0;
    bottom: 0;
    width: 600px;
    height: 343px;
  }
</style>
</head>
<body>
  <section class="card card-front" aria-label="Card front">
    <div class="brand">
      <div class="brand-square"></div>
      <div class="brand-name">VERODEX</div>
    </div>
  </section>

  <section class="card card-back" aria-label="Card back">
    <svg class="wave" viewBox="0 0 600 343" aria-hidden="true">
      <defs>
        <linearGradient id="waveFill" x1="0" y1="1" x2="1" y2="0">
          <stop offset="0" stop-color="#63c9dc"/>
          <stop offset="0.5" stop-color="#2fb3e6"/>
          <stop offset="1" stop-color="#3f6bb8"/>
        </linearGradient>
      </defs>
      <path d="M0,312 C160,336 320,300 450,210 C510,168 560,148 600,140 L600,343 L0,343 Z" fill="url(#waveFill)"/>
      <path d="M0,296 C160,318 320,282 450,192 C510,150 560,128 600,120" fill="none" stroke="#1b2a4a" stroke-width="6"/>
    </svg>

    <div class="back-brand">
      <div class="brand-square"></div>
      <div class="brand-name">VERODEX</div>
    </div>

    <div class="edge-tab"></div>
    <div class="person">
      <div class="person-name">DANIEL <span class="surname">HARTLEY</span></div>
      <div class="person-title">Co-Founder</div>
    </div>

    <ul class="contact">
      <li>
        <svg viewBox="0 0 16 16"><path d="M3 1 L6 1 L7 5 L5 6.5 C6 9 7 10 9.5 11 L11 9 L15 10 L15 13 C15 14 14 15 13 15 C6 15 1 10 1 3 C1 2 2 1 3 1 Z" fill="#35b6ea"/></svg>
        <span>555-210-4836</span>
      </li>
      <li>
        <svg viewBox="0 0 16 16"><rect x="1" y="3" width="14" height="10" fill="#35b6ea"/><path d="M1 3 L8 9 L15 3" fill="none" stroke="#fff" stroke-width="1.4"/></svg>
        <span>info@verodex.com</span>
      </li>
      <li>
        <svg viewBox="0 0 16 16"><circle cx="8" cy="8" r="7" fill="#35b6ea"/><path d="M1 8 H15 M8 1 C5 4 5 12 8 15 M8 1 C11 4 11 12 8 15" fill="none" stroke="#fff" stroke-width="1"/></svg>
        <span>www.verodex.com</span>
      </li>
    </ul>
  </section>
</body>
</html>
```